ZestoBayHub E-Commence Business Needs a New Launch Ad Banner Design for our website

We need a banner ad design for our new company based in Singapore called ZestoBayHub. Our business is targeted in helping Local Small Medium Enterprise (SME) to reach out to wider consumers base. We offered SME the platform to list their products and complete the sales and delivery cycle on their behalf.

So what do we sell?
- When we launch the e-Commence website on 15 October 2014, we have the following products categories i.e. Photo Frame, Photo Album, Clocks, Wall Arts, Jewellery Storages Boxes, Bags, Mugs, Throw Pillow, Rugs and Soft Toys.

So what do we need?
- We need a Banner Ad Design that will be place on our e-Commence website to announce Opening Sales promotion of 25% Discount Off All Items valid till 31 December 2014, 2359hrs. Terms & Condition Apply.

- I have provided the existing mock up design on our webpage name "1_home.jpg" so that your design can fit the overall look and feel for our website.

- We have also provided 21 photos of all our product ranges. Please use or edit these photo if required for the Banner Ad design.

- The moving panel space allocated on our website was set at 1181px by 469px.

Thank you.

Target Market(s)

Medium to Up market consumer, ASEAN consumer market, targeting age group from 15yrs to 45yrs consumer.

Industry/Entity Type

Business

Font styles to use
Sans Serif

Requirements
Must have
• Clarity of the marketing message
Should not have
• Clustering feeling

```html
<!DOCTYPE html>
<html lang="en">
<head>
<meta charset="utf-8">
<title>ZestoBayHub Opening Sale Banner</title>
<link rel="stylesheet" href="https://fonts.googleapis.com/css2?family=Open+Sans:wght@600;700&family=Arimo:wght@400;700&family=Arvo:wght@700&display=swap">
<style>
  :root {
    --sky: #1aa6e8;
    --sale-orange: #f2694a;
    --white: #ffffff;
    --ink: #111111;
    --brand-navy: #1c3a78;
    --tagline-green: #6bb33a;
    --offer-red: #d11a1a;
    --ribbon-grey: #8a8a8a;
  }
  * { margin: 0; padding: 0; box-sizing: border-box; }
  html, body { width: 1200px; height: 477px; overflow: hidden; background: var(--white); }
  .banner {
    position: relative;
    width: 1200px;
    height: 477px;
    background: var(--sky);
    overflow: hidden;
    font-family: "Open Sans", Arial, sans-serif;
  }
  .offer-panel { position: absolute; inset: 0; }
  .corner-ribbon { position: absolute; left: 0; top: 0; }
  .headline {
    position: absolute;
    left: 100px;
    top: -8px;
    width: 690px;
    text-align: center;
    color: var(--sale-orange);
    font-weight: 700;
    font-size: 72px;
    letter-spacing: 1px;
    line-height: 1;
  }
  .subheadline {
    position: absolute;
    left: 100px;
    top: 76px;
    width: 690px;
    text-align: center;
    color: var(--white);
    font-weight: 700;
    font-size: 44px;
    line-height: 1.1;
  }
  .product {
    position: absolute;
    border-radius: 6px;
  }
  .product--harness { left: 0; top: 152px; width: 135px; height: 200px; background: linear-gradient(#f08a2c, #3a6cc0); }
  .product--frames { left: 6px; top: 340px; width: 155px; height: 137px; background: linear-gradient(#f4f4f4, #e8c9a8); }
  .product--vintage-clock { left: 120px; top: 318px; width: 150px; height: 159px; border-radius: 50%; background: radial-gradient(#d9c9a0, #6a4a3a); }
  .product--grinder { left: 243px; top: 255px; width: 58px; height: 212px; background: linear-gradient(90deg, #8c8c8c, #e6e6e6, #7a7a7a); }
  .product--wall-clock { left: 300px; top: 280px; width: 185px; height: 185px; border-radius: 50%; background: radial-gradient(#ffffff 60%, #b8b8b8); }
  .product--jewel-safe { left: 400px; top: 278px; width: 110px; height: 180px; border-radius: 0 90px 90px 0; background: #16161e; }
  .product--pillow { left: 462px; top: 235px; width: 220px; height: 225px; background: linear-gradient(#f5d84a, #ee6a9a 40%, #7fd36a 70%, #a4e05a); }
  .product--shoe { left: 505px; top: 300px; width: 150px; height: 150px; background: linear-gradient(#f2a4a4, #e06060); }
  .product--bin { left: 668px; top: 232px; width: 108px; height: 225px; background: linear-gradient(#555a60 30%, #3a7fd0 31%); border-radius: 20px 20px 10px 10px; }
  .product--toy { left: 640px; top: 336px; width: 110px; height: 141px; background: linear-gradient(#2a2a2a 55%, #d42a3a 56%); border-radius: 40px 40px 6px 6px; }
  .side-panel { position: absolute; left: 0; top: 0; }
  .brand {
    position: absolute;
    left: 898px;
    top: 85px;
    display: flex;
    align-items: center;
    gap: 10px;
  }
  .brand-mark { width: 34px; height: 34px; background: var(--brand-navy); }
  .brand-name {
    font-family: "Open Sans", Arial, sans-serif;
    font-weight: 600;
    font-size: 32px;
    color: var(--brand-navy);
  }
  .tagline {
    position: absolute;
    left: 920px;
    top: 140px;
    font-family: "Arimo", Arial, sans-serif;
    font-size: 28px;
    color: var(--tagline-green);
  }
  .discount {
    position: absolute;
    left: 835px;
    top: 232px;
    width: 365px;
    text-align: center;
    font-family: "Arvo", Georgia, serif;
    font-weight: 700;
    font-size: 68px;
    color: var(--offer-red);
    letter-spacing: 1px;
  }
  .terms {
    position: absolute;
    left: 935px;
    top: 412px;
    width: 230px;
    text-align: center;
    font-family: "Arimo", Arial, sans-serif;
    font-weight: 700;
    font-size: 12.5px;
    line-height: 2.3;
    color: var(--ink);
  }
</style>
</head>
<body>
  <div class="banner">
    <div class="product product--harness" role="img" aria-label="Orange and blue baby walking harness"></div>
    <div class="product product--vintage-clock" role="img" aria-label="Vintage round wall clock with Roman numerals"></div>
    <div class="product product--frames" role="img" aria-label="White LOVE photo frame set with family photos"></div>
    <div class="product product--grinder" role="img" aria-label="Stainless steel pepper grinder"></div>
    <div class="product product--jewel-safe" role="img" aria-label="Open clock jewellery storage box with watches"></div>
    <div class="product product--wall-clock" role="img" aria-label="White modern wall clock"></div>
    <div class="product product--pillow" role="img" aria-label="Striped colourful throw pillow on green rug"></div>
    <div class="product product--shoe" role="img" aria-label="Pink high-heel shoe ornament"></div>
    <div class="product product--bin" role="img" aria-label="Blue and grey sensor waste bin"></div>
    <div class="product product--toy" role="img" aria-label="Black plush toy in red shirt"></div>

    <svg class="side-panel" width="1200" height="477" viewBox="0 0 1200 477" aria-hidden="true">
      <path d="M875 0 Q805 238 875 477 L1200 477 L1200 0 Z" fill="#ffffff" stroke="#111111" stroke-width="1.5"/>
    </svg>

    <svg class="corner-ribbon" width="110" height="110" viewBox="0 0 110 110" aria-hidden="true">
      <polygon points="0,50 50,0 82,0 0,82" fill="#8a8a8a"/>
      <polygon points="0,54 54,0 78,0 0,78" fill="#f2f2f2"/>
      <text x="33" y="45" transform="rotate(-45 33 45)" text-anchor="middle" font-family="Open Sans, Arial, sans-serif" font-weight="700" font-size="14" fill="#222222">OFFER!!</text>
    </svg>

    <h1 class="headline">SALE! SALE! SALE!</h1>
    <p class="subheadline">25% Discount Off All Items</p>

    <div class="brand">
      <span class="brand-mark"></span>
      <span class="brand-name">ZestoBayHub</span>
    </div>
    <p class="tagline">Everything You Need</p>
    <p class="discount">25% OFF</p>
    <p class="terms">valid till 31 December 2014,<br>2359hrs. Terms &amp; Condition Apply</p>
  </div>
</body>
</html>
```